Personal training and nutrition business needs business card design

We need a business card that outlays our services and invites potential customers to join our team and take the first step to a healthier and more enjoyable life. We cater for any level of fitness and specialize in weight loss and conditioning, strength training, muscle gain and strength endurance. Whether you are just starting off or need some help getting to the next level of your journey we are here to get the job done.
We specialize in one on one or one on two personal training sessions and each program will be custom made to suit individual fitness goals of our clients

```html
<!DOCTYPE html>
<html lang="en">
<head>
<meta charset="UTF-8">
<title>Stride &amp; Core – Business Card</title>
<link rel="stylesheet" href="https://fonts.googleapis.com/css2?family=Lato:wght@400;700;900&family=Oswald:wght@400&display=swap">
<style>
  :root {
    --backdrop: #242424;
    --card-white: #ffffff;
    --ink: #1a1a1a;
    --ink-soft: #3b3b3b;
    --purple: #7d45a6;
    --purple-deep: #6b3f9e;
    --orchid: #b461ad;
    --rule: #9a9a9a;
  }
  * { box-sizing: border-box; margin: 0; padding: 0; }
  html, body { width: 1200px; height: 1108px; overflow: hidden; }
  body {
    background: var(--backdrop);
    font-family: "Lato", sans-serif;
    position: relative;
  }
  .card {
    position: absolute;
    top: 204px;
    width: 420px;
    height: 700px;
    border-radius: 26px;
    overflow: hidden;
  }
  .card-front {
    left: 150px;
    background: var(--card-white);
    display: flex;
    flex-direction: column;
    align-items: center;
    padding-top: 150px;
    text-align: center;
  }
  .card-back { left: 630px; }

  .brand {
    display: flex;
    align-items: center;
    gap: 14px;
  }
  .brand-square {
    width: 22px; height: 22px;
    background: var(--purple);
  }
  .brand-name {
    font-family: "Lato", sans-serif;
    font-weight: 900;
    font-size: 42px;
    letter-spacing: 1px;
    color: var(--ink);
    text-transform: uppercase;
  }
  .tagline {
    margin-top: 18px;
    font-family: "Oswald", sans-serif;
    font-size: 15px;
    letter-spacing: 1.5px;
    color: var(--orchid);
    text-transform: uppercase;
  }
  .person-name {
    margin-top: 44px;
    font-weight: 700;
    font-size: 33px;
    color: var(--purple);
    text-transform: uppercase;
    letter-spacing: 0.5px;
  }
  .person-role {
    margin-top: 2px;
    font-size: 22px;
    color: var(--ink-soft);
  }
  .icon-rule {
    margin-top: 22px;
    width: 300px;
    display: flex;
    align-items: center;
    gap: 8px;
  }
  .icon-rule .line { flex: 1; height: 1px; background: var(--rule); }
  .icon-box {
    width: 32px; height: 32px;
    background: var(--purple);
    border-radius: 4px;
    display: flex; align-items: center; justify-content: center;
  }
  .contact-list {
    margin-top: 14px;
    list-style: none;
    font-size: 21px;
    line-height: 1.4;
    color: var(--ink-soft);
  }
  .divider {
    margin-top: 14px;
    width: 300px; height: 1px;
    background: var(--rule);
  }
  .address {
    margin-top: 14px;
    font-size: 21px;
    line-height: 1.4;
    color: var(--ink-soft);
    font-style: normal;
  }

  .back-pattern {
    position: absolute; inset: 0;
    background: linear-gradient(180deg, var(--orchid) 0%, #9a55a8 45%, var(--purple-deep) 100%);
  }
  .back-mark {
    position: absolute;
    right: 60px;
    bottom: 150px;
    display: flex; align-items: center; gap: 8px;
  }
  .back-mark .brand-square { width: 12px; height: 12px; background: var(--card-white); }
  .back-mark .brand-name { font-size: 18px; color: var(--card-white); }
</style>
</head>
<body>
  <section class="card card-front">
    <div class="brand">
      <span class="brand-square"></span>
      <span class="brand-name">Stride &amp; Core</span>
    </div>
    <p class="tagline">Personal Training. Nutrition. Motivation</p>

    <h1 class="person-name">Marcus Hale</h1>
    <p class="person-role">Managing Director</p>

    <div class="icon-rule">
      <span class="line"></span>
      <span class="icon-box" aria-label="Phone">
        <svg width="18" height="18" viewBox="0 0 24 24"><path fill="#fff" d="M6.6 10.8a15.1 15.1 0 0 0 6.6 6.6l2.2-2.2c.3-.3.7-.4 1-.2 1.1.4 2.3.6 3.6.6.6 0 1 .4 1 1V20c0 .6-.4 1-1 1C10.6 21 3 13.4 3 4c0-.6.4-1 1-1h3.5c.6 0 1 .4 1 1 0 1.3.2 2.5.6 3.6.1.3 0 .7-.2 1z"/></svg>
      </span>
      <span class="icon-box" aria-label="Email">
        <svg width="18" height="18" viewBox="0 0 24 24"><rect x="3" y="5" width="18" height="14" fill="none" stroke="#fff" stroke-width="2"/><path d="M3 5l9 8 9-8" fill="none" stroke="#fff" stroke-width="2"/></svg>
      </span>
      <span class="icon-box" aria-label="Website">
        <svg width="18" height="18" viewBox="0 0 24 24"><circle cx="12" cy="12" r="9" fill="none" stroke="#fff" stroke-width="2"/><path d="M3 12h18M12 3c3 3 3 15 0 18M12 3c-3 3-3 15 0 18" fill="none" stroke="#fff" stroke-width="1.5"/></svg>
      </span>
      <span class="line"></span>
    </div>

    <ul class="contact-list">
      <li>044-210 987 654</li>
      <li>info@strideandcore.com</li>
      <li>www.strideandcore.com</li>
    </ul>
    <div class="divider"></div>
    <address class="address">18, Harbour Road<br>20931, Northvale</address>
  </section>

  <section class="card card-back">
    <div class="back-pattern" role="img" aria-label="Repeating pattern of faint brand marks over a purple gradient"></div>
    <div class="back-mark">
      <span class="brand-square"></span>
      <span class="brand-name">Stride &amp; Core</span>
    </div>
  </section>
</body>
</html>
```